Modern design company business card design

We are a design oriented construction firm. The owner is an architect and licensed General Contractor and accomplished furniture designer. We do new home construction and large scale remodeling and office design. We would like a design for our new business cards that is clean and modern, but relatable. We like the bright green color of our logo mixed with different shades of grey. We're also open to reinterpreting the logo.

Target Market(s)

Potential design clients,
Construction clients

Industry/Entity Type

Architecture

Contact Information for Business Card

Tall Maple Design | Build Inc. (optional with logo, Inc. optional)Jeffrey MorganOwner (optional)317.555.0148 cell317.431.8056 officejmorgan@greensquareinc.comwww.greensquareinc.com

Font styles to use
Sans Serif
Other font styles liked:
• Avenir

Requirements
Nice to have
• I like designs that have some continuity between the front and back, i.e. similar layouts or graphic elements that wrap around the card. I tend to prefer horizontal over vertical, but that's not a have to. I also tend to prefer white or recycled paper.

```html
<!DOCTYPE html>
<html lang="en">
<head>
<meta charset="utf-8">
<title>Tall Maple Design | Build – Business Cards</title>
<link rel="stylesheet" href="https://fonts.googleapis.com/css2?family=Nunito+Sans:wght@400;600;700&display=swap">
<style>
  :root {
    --backdrop: #d9d9d6;
    --card-white: #fbfbfb;
    --green-light: #c4de6a;
    --green-mid: #a3d262;
    --green-deep: #6cc24f;
    --grey-text: #8c8c8c;
    --ink: #1e1e1e;
    --shadow: rgba(0, 0, 0, 0.22);
  }
  * { margin: 0; padding: 0; box-sizing: border-box; }
  html, body { width: 1200px; height: 844px; overflow: hidden; }
  body {
    background: var(--backdrop);
    font-family: "Nunito Sans", sans-serif;
    position: relative;
  }
  .card {
    position: absolute;
    width: 500px;
    height: 286px;
    border-radius: 3px;
    box-shadow: 0 14px 30px var(--shadow);
  }
  .card--front {
    left: 70px;
    top: 390px;
    background: var(--card-white);
  }
  .card--back {
    left: 630px;
    top: 170px;
    background: linear-gradient(160deg, var(--green-light) 0%, var(--green-mid) 50%, var(--green-deep) 100%);
  }
  .brand {
    position: absolute;
    left: 250px;
    top: 62px;
    font-size: 17px;
    font-weight: 600;
    letter-spacing: 0.08em;
    text-transform: uppercase;
    color: var(--grey-text);
    line-height: 1.25;
  }
  .back__name {
    position: absolute;
    left: 150px;
    top: 108px;
    font-size: 24px;
    font-weight: 600;
    letter-spacing: 0.08em;
    text-transform: uppercase;
    color: #ffffff;
    line-height: 1.25;
  }
  .contact {
    position: absolute;
    left: 32px;
    bottom: 26px;
  }
  .contact__name {
    font-size: 17px;
    font-weight: 700;
    color: var(--green-mid);
  }
  .contact__role {
    font-size: 12px;
    color: var(--ink);
    margin-bottom: 12px;
  }
  .contact__list { list-style: none; }
  .contact__item {
    display: flex;
    align-items: center;
    gap: 16px;
    font-size: 14px;
    color: var(--ink);
    line-height: 19px;
  }
  .contact__icon { width: 11px; height: 11px; flex: none; }
</style>
</head>
<body>

<section class="card card--front" aria-label="Business card, front">
  <p class="brand">Tall Maple<br>Design | Build</p>

  <div class="contact">
    <p class="contact__name">Dennis Holloway</p>
    <p class="contact__role">Owner</p>
    <ul class="contact__list">
      <li class="contact__item">
        <svg class="contact__icon" viewBox="0 0 12 12" aria-hidden="true"><path fill="#8cc540" d="M2.4 0.8l2 2-1 1.3c.6 1.4 1.6 2.4 3 3l1.3-1 2 2-1.2 1.8C5 9.8 1.9 6.8 0.6 2z"/></svg>
        <span>317.555.0172</span>
      </li>
      <li class="contact__item">
        <svg class="contact__icon" viewBox="0 0 12 12" aria-hidden="true"><rect x="2.5" y="0.5" width="7" height="11" rx="1.2" fill="none" stroke="#8cc540" stroke-width="1.2"/><circle cx="6" cy="9.6" r="0.7" fill="#8cc540"/></svg>
        <span>317.555.0148</span>
      </li>
      <li class="contact__item">
        <svg class="contact__icon" viewBox="0 0 12 12" aria-hidden="true"><rect x="0.5" y="2" width="11" height="8" fill="#8cc540"/><path d="M0.5 2l5.5 4.5L11.5 2" fill="none" stroke="#fff" stroke-width="1"/></svg>
        <span>dholloway@tallmapleinc.example</span>
      </li>
      <li class="contact__item">
        <svg class="contact__icon" viewBox="0 0 12 12" aria-hidden="true"><g fill="none" stroke="#8cc540" stroke-width="1.4"><rect x="0.8" y="5" width="6" height="3.4" rx="1.7" transform="rotate(-45 3.8 6.7)"/><rect x="5.2" y="3.6" width="6" height="3.4" rx="1.7" transform="rotate(-45 8.2 5.3)"/></g></svg>
        <span>www.tallmapleinc.example</span>
      </li>
    </ul>
  </div>
</section>

<section class="card card--back" aria-label="Business card, back">
  <p class="back__name">Tall Maple<br>Design | Build</p>
</section>

</body>
</html>
```